Website Redesign Project

Brightwater Delivery Partners provides project management and project controls consultancy services to companies in many industry sectors, within Australia and overseas. My company has been developing a business brand through forging strong business relationships within industry. We provide innovative tools, concepts and solutions to management teams to assist them in better plan and managing there project portfolios.
SECTORS OF INDUSTRY WE SERVICE
★Oil & Gas
★Minerals & Metals
★Petrochemical
★Manufacturing
★Building & Construction
★Telecommunications
★Rail
★Civil
OLD WEBSITE
My old website www.brightwaterdeliverypartners-demo.com.au needs a complete overhaul in terms of how the web pages look and feel. I am trying to get away from the grey, washed out look as it is uninviting and dull. My clients commented that my webpage does not reflect who I am as a company or my core values. Think total redesign
DESIGN
I would like a webpage design that is modern and has a corporate image. It must be elegant, classy, and have an overall glossy appearance. I want something exciting that creates some excellent feedback from clients. It needs to have a savvy appearance and an attitude of a market leader. A generic website template cannot be used as I provide a unique service to clients. I do not need a website design that looks like my compeditors, I want something that stands out in the crowd and effectivly markets my bussinesses brand. I want my website to represent quality, so only high resolution images that are clear, sharp and in focus can be used. With this design, throw your standard webpage design concepts out the window, as I want something fresh, innovative, exciting and inviting. The overall design should appear uncluttered as all content needs to be there for a reason, so think functional.
It must be professional and of the highest calibre as my clients expect nothing less. I provide clients with innovative tools, concepts and solutions, so the design needs to be edgy and creative to align with my company’s core business services. The new design must promote the company’s brand and us as a market leader. It must communicate that we service many industry sectors and reflect our company’s creativity, vision, energy and drive.
WEBPAGE WRITTEN CONTENT
I am happy with the written content on each page within my old website. You may arrange the text how you see fit within the new design. On the main page of my old website the text is under scored, I am not a big fan of this. I currently do not like the format the text is in, I am looking for a formatt that is easy to read, looks flattering and pleasing to the eye.
MAIN PAGE DESIGN
The main page design needs to focus on my company as a brand, it must promote that I service many industry sectors. My old webpage had me pigeon holed as only providing services to oil and gas. This is incorrect as I service oil & gas, metals and minerals, Petrochemical, Manufacturing, Building & Construction, Telecommunications, Rail and civil.
WEBPAGE COLUR PREFERENCE
Prefer a white background with plenty of colour
TESTIMONIAL TAB
The testimonial tab on the task bar can be removed as it is no longer required.
FINISHED PRODUCT
The finished product will be uploaded by you to a nominated web hosting account. I will need a copy of all files associated with the design. A copy of the finished product will also be provided in formats that can me imported to Xara Pro Designer as I will update my website in 6 months or so using this tool.
Updates
I have updated the design brief after recieving feedback from several designers
Thanks
Reason: Some designers have asked for more time
Hi All
I have just launched another project called "brightwater delivery partners business card redesign project", you are all welcome to join this project.
Thanks
Target Market(s)
★Oil and Gas
★Mining and Resources
★Building and infrastructure
★Petrochemical
★Civil and roads
★Rail
Industry/Entity Type
Industry
Requirements
Must have
- ★Draw you in
★Hold your attention
★Identify company brand
★Highlight skills experience and expertise
★Be a unique design not generic
Should not have
- ★The webpage design should not be old fashioned
★ The design should not be based off a generic design template
★The webpage should not be cluttered; everything needs to be there for a reason.

```html
<!DOCTYPE html>
<html lang="en">
<head>
<meta charset="utf-8">
<title>Brightwater Delivery Partners</title>
<link href="https://fonts.googleapis.com/css2?family=Source+Sans+3:ital,wght@0,400;0,600;0,700;1,400&display=swap" rel="stylesheet">
<style>
:root{
  --red:#e31b23;
  --page:#f1f1f1;
  --panel:#e6e6e6;
  --ink:#2b2b2b;
  --muted:#555;
  --rule:#d4d4d4;
  --btn:#555a60;
}
*{margin:0;padding:0;box-sizing:border-box}
html,body{width:1146px;height:1200px;overflow:hidden}
body{background:var(--page);font-family:"Source Sans 3",sans-serif;color:var(--ink);position:relative}
.abs{position:absolute}
.top-band{left:172px;top:0;width:802px;height:6px;background:var(--red)}
.brand{left:172px;top:30px;display:flex;align-items:center;gap:8px}
.brand-dot{width:34px;height:34px;border-radius:50%;background:var(--red)}
.brand-name{font-size:19px;font-weight:700;color:var(--red);letter-spacing:-.2px;line-height:1}
.brand-tag{left:214px;top:68px;font-size:7px;color:#333}
.search{left:548px;top:63px;width:183px;height:21px;background:#fff;border:1px solid #d6d6d6;border-radius:3px;font-size:8.5px;color:#777;padding:5px 9px}
.search svg{position:absolute;right:6px;top:4px}
.contact-line{left:763px;display:flex;align-items:center;gap:8px;font-size:10px;color:var(--red)}
.rule{height:1px;background:var(--rule)}
.main-nav{left:172px;top:104px;width:802px;height:49px;border-top:2px solid #dedede;display:flex;justify-content:space-between;align-items:center;padding:0 15px 0 15px;font-size:10px;color:#222}
.hero{left:172px;top:153px;width:802px;height:330px;background:linear-gradient(120deg,#d8c6ad 0%,#efece7 45%,#c8b49a 100%)}
.hero-caption{left:172px;top:362px;width:395px;height:91px;background:var(--red);color:#fff;padding:13px 24px}
.hero-caption h1{font-size:21px;font-weight:400;letter-spacing:-.2px;line-height:1.1}
.hero-caption p{font-size:8.2px;font-weight:700;line-height:18px;margin-top:5px;letter-spacing:-.1px}
.hero-arrows{position:absolute;right:16px;top:16px}
.services{left:172px;top:492px;width:186px}
.services h2{height:29px;background:linear-gradient(#dcdcdc,#e8e8e8);font-size:11px;font-weight:400;padding:8px 15px;color:#222}
.services ul{list-style:none;margin-top:10px}
.services li{font-size:8.2px;height:23px;padding-left:14px;position:relative;color:#222;line-height:12px}
.services li::before{content:"›";position:absolute;left:11px;top:-2px;font-size:12px;color:#666;margin-left:-8px}
.sectors{left:377px;top:484px;width:597px;height:238px;background:var(--panel)}
.sector{position:absolute;top:17px;width:172px}
.sector h3,.block-title{font-size:12.5px;font-weight:400;color:var(--red);letter-spacing:-.2px}
.sector .photo{width:171px;height:73px;margin-top:7px}
.sector p,.body-text{font-size:8.4px;line-height:14.7px;color:var(--muted)}
.sector p{margin-top:12px}
.btn{display:block;width:73px;height:22px;border-radius:2px;background:linear-gradient(#6a6f75,#4b4f55);color:#e8e8e8;font-size:8px;text-align:center;line-height:22px}
.sector .btn{margin-top:11px}
.pager{position:absolute;display:flex;gap:6px}
.block-title.lg{font-size:15px}
.photo-fill{border:0}
.quote-mark{font-family:Georgia,serif;font-size:38px;color:#c9c9c9;line-height:1}
.testimonial-head{font-size:8.4px;color:var(--red);font-weight:600}
.avatar{width:56px;height:49px;border:2px solid #fff;box-shadow:0 0 0 1px #ccc;background:linear-gradient(#e4d6c9,#c7b29e)}
.footer-nav{left:172px;top:1131px;width:802px;display:flex;justify-content:center;font-size:7.4px;color:#222}
.footer-nav span{padding:0 12px;border-right:1px solid #555;line-height:8px}
.footer-nav span:last-child{border-right:0}
.copyright{left:172px;top:1153px;width:802px;text-align:center;font-size:7.2px;color:#333}
.social{width:25px;height:25px;border-radius:50%}
</style>
</head>
<body>
<div class="abs top-band"></div>

<div class="abs brand"><span class="brand-dot"></span><span class="brand-name">BRIGHTWATER DELIVERY PARTNERS</span></div>
<div class="abs brand-tag">Providing Effective Project Controls and Management Solutions</div>

<div class="abs search">Search :
  <svg width="12" height="12" viewBox="0 0 12 12"><circle cx="5" cy="5" r="3.8" fill="none" stroke="#bbb" stroke-width="1.3"/><line x1="7.8" y1="7.8" x2="11" y2="11" stroke="#bbb" stroke-width="1.5"/></svg>
</div>

<div class="abs contact-line" style="top:46px">
  <svg width="12" height="10" viewBox="0 0 12 10"><path d="M1 3 Q6 -1 11 3 L10 4.5 8 3.6 8 2.6 Q6 2 4 2.6 L4 3.6 2 4.5Z M3 5 H9 L10 9.5 H2Z" fill="#777"/></svg>
  <span>CALL : + 61 0400 555 019</span>
</div>
<div class="abs contact-line" style="top:71px">
  <svg width="12" height="9" viewBox="0 0 12 9"><rect x=".5" y=".5" width="11" height="8" fill="#777"/><path d="M.5 .5 6 5 11.5 .5" fill="none" stroke="#eee"/></svg>
  <span>jordan.hale@brightwaterdp-demo.com.au</span>
</div>

<nav class="abs main-nav">
  <span>ABOUT US</span><span>EXPERTISE</span><span>KNOWLEDGE</span><span>EXPERIENCE</span><span>PROJECTS</span><span>FOCUS</span><span>TESIMONIALS</span><span>RECRUITMENT</span><span>CONTACT</span>
</nav>

<div class="abs hero" role="img" aria-label="Two engineers in hard hats reviewing construction plans"></div>
<div class="abs hero-caption">
  <h1>BRIGHTWATER DELIVERY PARTNERS</h1>
  <p>I PROVIDE SERVICES TO COMPANIES IN THE MINING AND OIL AND GAS SECTOR TO ENABLING<br>THEM TO PLAN AND MANAGE THEIR CONSTRUCTION PROJECTS MORE EFFECTIVELY.</p>
  <svg class="hero-arrows" width="30" height="12" viewBox="0 0 30 12"><path d="M6 1 1 6 6 11M22 1 27 6 22 11" fill="none" stroke="#fff" stroke-width="2"/></svg>
</div>

<aside class="abs services">
  <h2>SERVICES</h2>
  <ul>
    <li>OIL &amp; GAS</li><li>MINERALS &amp; METALS</li><li>PETROCHEMICAL</li><li>MANUFACTURING</li><li>BUILDING &amp; CONSTRUCTION</li><li>TELECOMMUNICATIONS</li><li>RAIL</li><li>CIVIL</li>
  </ul>
</aside>

<section class="abs sectors">
  <div class="sector" style="left:15px">
    <h3>OIL &amp; GAS</h3>
    <div class="photo" role="img" aria-label="Offshore oil platform at sea" style="background:linear-gradient(#9cc3e6 0%,#d9e8f4 55%,#1f4f85 60%,#163c6a 100%)"></div>
    <p>I provide services to companies in the mining and oil and gas sector to enabling them to plan and manage their construction projects more effectively.</p>
    <span class="btn">Read More</span>
  </div>
  <div class="sector" style="left:212px">
    <h3>BUILDING &amp; CONSTRUCTION</h3>
    <div class="photo" role="img" aria-label="Architectural model of houses on plans" style="background:linear-gradient(#ffffff,#d2d4d6 70%,#9a9ea3)"></div>
    <p>I provide services to companies in the mining and oil and gas sector to enabling them to plan and manage their construction projects more effectively.</p>
    <span class="btn">Read More</span>
  </div>
  <div class="sector" style="left:408px">
    <h3>PETROCHEMICAL</h3>
    <div class="photo" role="img" aria-label="Petrochemical plant lit at night" style="background:linear-gradient(100deg,#3a1e08,#c8731c 45%,#5a2c0c 75%,#2a1a10)"></div>
    <p>I provide services to companies in the mining and oil and gas sector to enabling them to plan and manage their construction projects more effectively.</p>
    <span class="btn">Read More</span>
  </div>
  <svg class="pager" style="left:565px;top:129px;position:absolute" width="24" height="10" viewBox="0 0 24 10"><path d="M5 1 1 5 5 9M18 1 22 5 18 9" fill="none" stroke="#999" stroke-width="1.5"/></svg>
</section>
<svg class="abs" style="left:940px;top:501px" width="24" height="10" viewBox="0 0 24 10"><path d="M5 1 1 5 5 9M18 1 22 5 18 9" fill="none" stroke="#999" stroke-width="1.5"/></svg>

<!-- Welcome -->
<h2 class="abs block-title lg" style="left:173px;top:750px">WELCOME TO BRIGHTWATER DELIVERY PARTNERS</h2>
<div class="abs photo-fill" role="img" aria-label="Two engineers in hard hats reading plans before office towers" style="left:172px;top:785px;width:287px;height:147px;background:linear-gradient(#4f7fb4,#a9c3dd 60%,#dfe6ee)"></div>
<p class="abs body-text" style="left:172px;top:938px;width:290px">I provide services to companies in the mining and oil and gas sector to enabling them to plan and manage their construction projects more effectively. This is achieved by evaluating the businesses practices and them implementing different tools and solutions.</p>
<p class="abs body-text" style="left:172px;top:1012px;width:290px">My clients are then able to plan and deliver their projects, on time and within their budgets. I am able to provide services to both large and small scale businesses within Australian and Overseas. I offer my clients value by providing, exceptional skills and expertise at a competitive market rate.</p>

<!-- Expertise -->
<h2 class="abs block-title lg" style="left:497px;top:750px">EXPERTISE</h2>
<div class="abs photo-fill" role="img" aria-label="Yellow hard hat, level and compass on blueprints" style="left:496px;top:785px;width:219px;height:98px;background:linear-gradient(110deg,#7d8f9e,#c7d2dc 45%,#e7b920 70%,#c9d3dc)"></div>
<p class="abs body-text" style="left:496px;top:896px;width:222px">I provide services to companies in the mining and oil and gas sector to enabling them to plan and manage their construction projects more effectively. This is achieved by evaluating the businesses practices.</p>
<span class="abs btn" style="left:497px;top:965px">Read More</span>

<!-- Testimonials -->
<h2 class="abs block-title lg" style="left:746px;top:750px">TESTIMONIALS</h2>
<svg class="abs" style="left:950px;top:756px" width="24" height="10" viewBox="0 0 24 10"><path d="M5 1 1 5 5 9M18 1 22 5 18 9" fill="none" stroke="#999" stroke-width="1.5"/></svg>
<div class="abs quote-mark" style="left:748px;top:780px">&ldquo;</div>
<div class="abs testimonial-head" style="left:775px;top:800px">I PROVIDE SERVICES TO COMPANIES :</div>
<p class="abs body-text" style="left:775px;top:818px;width:200px">I provide services to companies in the mining and oil and gas sector to enabling them to plan and manage their construction projects more effectively. This is achieved by evaluating the business practices.</p>
<div class="abs quote-mark" style="left:952px;top:894px">&rdquo;</div>
<div class="abs avatar" role="img" aria-label="Portrait of the client" style="left:766px;top:928px"></div>
<div class="abs testimonial-head" style="left:837px;top:932px;font-weight:400">MARCUS DELANE</div>
<div class="abs" style="left:837px;top:948px;font-size:8px;font-style:italic;color:#666">Organisor</div>
<div class="abs" style="left:837px;top:964px;font-size:8px;font-style:italic;color:#666">Posted on 20 may 2013</div>

<div class="abs rule" style="left:497px;top:1000px;width:218px"></div>
<div class="abs rule" style="left:755px;top:1000px;width:219px"></div>

<!-- Newsletter -->
<h2 class="abs block-title lg" style="left:497px;top:1009px">NEWSLETTER SIGNUP</h2>
<div class="abs" style="left:496px;top:1040px;font-size:8px;color:#333">GET OUR UPDAYED NEWS FROM EMAIL</div>
<div class="abs" style="left:496px;top:1060px;width:140px;height:22px;background:#fff;border:1px solid #d0d0d0;font-size:7px;color:#777;padding:6px 8px">ENTER YOUR EMAIL ID :</div>
<span class="abs btn" style="left:643px;top:1060px;width:72px;height:22px">Subscribe</span>

<!-- Follow -->
<h2 class="abs block-title lg" style="left:756px;top:1009px">FOLLOW US</h2>
<div class="abs" style="left:740px;top:1045px;width:98px;text-align:right;font-size:8px;line-height:15px;color:#333">CONNECT TO<br>OUR SOCIAL NETWORK</div>
<span class="abs social" style="left:850px;top:1047px;background:#2d6bb5"></span>
<span class="abs social" style="left:881px;top:1047px;background:#3fa6dc"></span>
<span class="abs social" style="left:912px;top:1047px;background:#1f7fa8"></span>
<span class="abs social" style="left:942px;top:1047px;background:#f0a229"></span>

<div class="abs" style="left:172px;top:1109px;width:802px;height:3px;background:#d0d0d0"></div>
<nav class="abs footer-nav">
  <span>ABOUT US</span><span>EXPERTISE</span><span>KNOWLEDGE</span><span>EXPERIENCE</span><span>PROJECTS</span><span>FOCUS</span><span>TESIMONIALS</span><span>RECRUITMENT</span><span>CONTACT</span>
</nav>
<div class="abs copyright">© COPYRIGHT 2013. BRIGHTWATER DELIVERY PARTNERS. ALL RIGHTS RESERVED</div>
</body>
</html>
```